A new presentation to our clients

we are a Real Estate agency, our website is www.lumibrasa.com and it’s time to have a new, fashion and remarcable Business Card. we want to differentiate ourselves from other companies so we want a business card that differentiates us. we want the business card to impact our customers. in the competitive market that we have today, we have to be different and it is this difference that we seek

Target Market(s)

Real Estate Clients

Contact Information for Business Card

We search a totaly diferent card from the usual

Font styles to use
Sans Serif

Colors
e34197

Requirements
Must have
• Logo, adress, phone contact, e-mail, photo, and our website
Nice to have
• We would like to see a modern business card
Should not have
• Houses or building draws

```html
<!DOCTYPE html>
<html lang="en">
<head>
<meta charset="utf-8">
<title>Lumibrasa Business Card</title>
<link rel="stylesheet" href="https://fonts.googleapis.com/css2?family=Bebas+Neue&family=Lato:wght@400;700&display=swap">
<style>
  :root {
    --backdrop: #252527;
    --card: #45474f;
    --accent: #e52f78;
    --text-light: #f2f2f4;
  }
  * { margin: 0; padding: 0; box-sizing: border-box; }
  html, body { width: 1200px; height: 1200px; overflow: hidden; }
  body { background: var(--backdrop); position: relative; font-family: 'Lato', sans-serif; }

  .card {
    position: absolute;
    left: 140px;
    width: 920px;
    height: 525px;
    background: var(--card);
    border-radius: 34px;
  }
  .card--front { top: 48px; }
  .card--back { top: 640px; }

  .identity {
    position: absolute;
    right: 494px;
    top: 262px;
    text-align: right;
  }
  .identity__name {
    font-family: 'Bebas Neue', sans-serif;
    font-size: 54px;
    line-height: 1;
    color: var(--text-light);
    letter-spacing: 0;
  }
  .identity__role {
    font-size: 24px;
    line-height: 1;
    color: var(--accent);
    margin-top: 2px;
  }

  .contacts {
    position: absolute;
    left: 496px;
    top: 262px;
    list-style: none;
  }
  .contacts__item {
    display: flex;
    align-items: center;
    height: 29.5px;
    font-size: 19px;
    color: var(--text-light);
  }
  .contacts__icon {
    width: 20px;
    height: 20px;
    margin-right: 14px;
    flex: none;
  }

  .address {
    position: absolute;
    left: 0;
    right: 0;
    top: 448px;
    text-align: center;
    font-size: 21px;
    color: var(--text-light);
  }

  .brand-name {
    position: absolute;
    right: 60px;
    bottom: 62px;
    font-weight: 700;
    font-size: 100px;
    line-height: 1;
    color: var(--accent);
  }
</style>
</head>
<body>
  <section class="card card--front">
    <div class="identity">
      <h1 class="identity__name">Davi Roque Lemos</h1>
      <p class="identity__role">CEO/manager</p>
    </div>

    <ul class="contacts">
      <li class="contacts__item">
        <svg class="contacts__icon" viewBox="0 0 20 20" aria-hidden="true">
          <rect x="5" y="1" width="10" height="18" rx="2" fill="none" stroke="var(--accent)" stroke-width="2"/>
          <circle cx="10" cy="15.5" r="1.2" fill="var(--accent)"/>
        </svg>
        +55 - 214 - 3087
      </li>
      <li class="contacts__item">
        <svg class="contacts__icon" viewBox="0 0 20 20" aria-hidden="true">
          <rect x="1" y="4" width="18" height="12" fill="var(--accent)"/>
          <path d="M1 4 L10 11 L19 4" fill="none" stroke="var(--card)" stroke-width="1.5"/>
        </svg>
        hello@lumibrasa.com
      </li>
      <li class="contacts__item">
        <svg class="contacts__icon" viewBox="0 0 20 20" aria-hidden="true">
          <g fill="none" stroke="var(--accent)" stroke-width="1.4">
            <circle cx="10" cy="10" r="8"/>
            <ellipse cx="10" cy="10" rx="3.5" ry="8"/>
            <line x1="2" y1="10" x2="18" y2="10"/>
            <line x1="3.5" y1="6" x2="16.5" y2="6"/>
            <line x1="3.5" y1="14" x2="16.5" y2="14"/>
          </g>
        </svg>
        www.lumibrasa.com
      </li>
    </ul>

    <p class="address">Rua das Palmeiras 2480 Jardim Azul Lagoa, Brazil</p>
  </section>

  <section class="card card--back">
    <p class="brand-name">Lumibrasa</p>
  </section>
</body>
</html>
```